Verlindo Magician

I want the business card for my business to give to people who watch that later I will be employed to show magic here is my website http://www.verlindoillusions.example/I want the interesting design , i am very opened for formal and informal, I watch a lot of design so don't stick to the common shape and form but i hope it can also be produced the thing to write on will be the same as in picture that i will upload , i also will upload the logo for you that so can be easy to useDenis CostilleMagicianMAGICIAN BALSAMO 17 rue des Tilleuls - 25000 BESANÇON contact@verlindoillusions.example tel. 0381 946 157 tel. 0674 219 503

```html
<!DOCTYPE html>
<html lang="fr">
<head>
<meta charset="utf-8">
<title>Verlindo Magician – Business Card</title>
<link href="https://fonts.googleapis.com/css2?family=Questrial&display=swap" rel="stylesheet">
<style>
  :root {
    --stage: #2a2a2a;
    --card: #ffffff;
    --card-tint: #f4f3f4;
    --ink: #141414;
    --ink-soft: #2b2b2b;
    --accent: #e0262b;
    --icon-box: #1c1c1c;
    --figure-dark: #111111;
    --figure-mid: #3a3a3a;
  }
  * { box-sizing: border-box; margin: 0; padding: 0; }
  html, body { width: 1200px; height: 895px; overflow: hidden; }
  body {
    background: var(--stage);
    font-family: "Questrial", "Century Gothic", sans-serif;
    color: var(--ink);
    position: relative;
  }
  .card {
    position: absolute;
    top: 293px;
    width: 540px;
    height: 309px;
    background: var(--card);
    box-shadow: 0 8px 24px rgba(0,0,0,.45);
    overflow: hidden;
  }
  .card--front {
    left: 40px;
    background: linear-gradient(180deg, var(--card) 0%, var(--card-tint) 100%);
  }
  .card--back { left: 620px; }

  .portrait {
    position: absolute;
    background: radial-gradient(ellipse at 50% 30%, var(--figure-mid) 0%, var(--figure-dark) 70%);
    border-radius: 48% 48% 12% 12% / 40% 40% 12% 12%;
  }
  .card--front .portrait { left: 190px; top: 34px; width: 160px; height: 172px; }
  .card--back .portrait  { left: 392px; top: 26px; width: 118px; height: 130px; }

  .brand-name {
    position: absolute;
    left: 0; right: 0; top: 228px;
    text-align: center;
    font-size: 26px;
    letter-spacing: 4px;
    color: var(--ink);
  }

  .holder {
    position: absolute;
    left: 40px; top: 148px;
  }
  .holder__name { font-size: 28px; letter-spacing: 1px; color: var(--ink); }
  .holder__role { font-size: 12px; letter-spacing: 1.5px; color: var(--ink-soft); margin-top: 2px; margin-left: 14px; }

  .contacts {
    position: absolute;
    left: 40px; top: 212px;
    list-style: none;
  }
  .contact {
    display: flex;
    align-items: center;
    gap: 12px;
    height: 30px;
  }
  .contact__icon {
    width: 24px; height: 24px;
    background: var(--icon-box);
    border-radius: 3px;
    display: flex; align-items: center; justify-content: center;
    flex: none;
  }
  .contact__icon svg { width: 14px; height: 14px; }
  .contact__text { font-size: 11.5px; line-height: 13px; color: var(--ink); letter-spacing: .3px; }
</style>
</head>
<body>

<section class="card card--front" aria-label="Card front">
  <div class="portrait" role="img" aria-label="Black and white illustration of the magician holding a playing card"></div>
  <p class="brand-name">VERLINDO MAGICIAN</p>
</section>

<section class="card card--back" aria-label="Card back">
  <div class="portrait" role="img" aria-label="Black and white illustration of the magician holding a playing card"></div>

  <div class="holder">
    <h1 class="holder__name">MARC RAVOULET</h1>
    <p class="holder__role">MAGICIAN</p>
  </div>

  <ul class="contacts">
    <li class="contact">
      <span class="contact__icon">
        <svg viewBox="0 0 24 24"><path fill="var(--accent)" d="M6.6 10.8a15 15 0 0 0 6.6 6.6l2.2-2.2a1 1 0 0 1 1-.25 11.4 11.4 0 0 0 3.6.57 1 1 0 0 1 1 1V20a1 1 0 0 1-1 1A17 17 0 0 1 3 4a1 1 0 0 1 1-1h3.5a1 1 0 0 1 1 1c0 1.25.2 2.45.57 3.6a1 1 0 0 1-.25 1z"/></svg>
      </span>
      <span class="contact__text">0381 946 157<br>0674 219 503</span>
    </li>
    <li class="contact">
      <span class="contact__icon">
        <svg viewBox="0 0 24 24" fill="none" stroke="var(--accent)" stroke-width="2"><circle cx="12" cy="12" r="9"/><ellipse cx="12" cy="12" rx="4" ry="9"/><path d="M3 12h18M5 7h14M5 17h14"/></svg>
      </span>
      <span class="contact__text">contact@verlindoillusions.example<br>verlindoillusions.example</span>
    </li>
    <li class="contact">
      <span class="contact__icon">
        <svg viewBox="0 0 24 24"><path fill="var(--accent)" d="M12 2a7 7 0 0 0-7 7c0 5.2 7 13 7 13s7-7.8 7-13a7 7 0 0 0-7-7zm0 9.5A2.5 2.5 0 1 1 12 6.5a2.5 2.5 0 0 1 0 5z"/></svg>
      </span>
      <span class="contact__text">17 rue des Tilleuls<br>25000 BESANÇON</span>
    </li>
  </ul>
</section>

</body>
</html>
```